Design a homepage graphic to show a system journey

We have a software package for parents to update student information and manage school excursions we have attached a concept we like but are open to other ideas so long as they fit the following criteria.
1 It needs to be landscape across the page
2. They are showing a series of processes, each step has its own colour, see below
2.1 The first process is a parent updating their own and students information and approving excursions
2.2 The school then creates and manages the excursion this includes a compliance component
2.3 The school conducts the activity it should show some activity type pictures
2.4 Students return safely to school
3 There can be text boxes within the image to clarify functionality
4. The picture should make anyone watching it understand there is a series of
linked processes the system provides i.e. a journey
There should be the ability to click on each component to link to a specific part of the pager lower down, e.g if the person wanted to look at the school part by clicking on the school it would take them to more information, that information already exists so is not required.
Please review the attached concept diagram and use this a potential guide.
Schools
1 page

```html
<!DOCTYPE html>
<html lang="en">
<head>
<meta charset="utf-8">
<title>School Excursion Journey</title>
<link rel="stylesheet" href="https://fonts.googleapis.com/css2?family=Montserrat:wght@400;500&display=swap">
<style>
  :root {
    --bg: #ffffff;
    --road: #4a545e;
    --road-line: #ffffff;
    --ink: #2f3438;
    --pink: #f98ac8;
    --olive: #a3b84f;
    --violet: #b85bc9;
    --sky: #10a8d8;
    --teal: #12c9a0;
    --amber: #fbc75a;
  }
  html, body {
    margin: 0;
    padding: 0;
    width: 1200px;
    height: 675px;
    overflow: hidden;
    background: var(--bg);
  }
  .journey {
    display: block;
    width: 1200px;
    height: 675px;
    font-family: "Montserrat", sans-serif;
  }
  .road { fill: none; stroke: var(--road); stroke-width: 56; }
  .road-line { fill: none; stroke: var(--road-line); stroke-width: 7; stroke-dasharray: 18 24; }
  .step-label { fill: var(--ink); font-size: 23px; font-weight: 400; letter-spacing: 0.5px; }
  .pin-ring { fill: #ffffff; stroke-width: 12; }
  .pin-number { fill: var(--ink); font-size: 36px; font-weight: 500; text-anchor: middle; dominant-baseline: central; }
  .pin--pink { fill: var(--pink); stroke: var(--pink); }
  .pin--olive { fill: var(--olive); stroke: var(--olive); }
  .pin--violet { fill: var(--violet); stroke: var(--violet); }
  .pin--sky { fill: var(--sky); stroke: var(--sky); }
  .pin--teal { fill: var(--teal); stroke: var(--teal); }
  .pin--amber { fill: var(--amber); stroke: var(--amber); }
  .pin .pin-ring { fill: #ffffff; }
  .scene { stroke: none; }
</style>
</head>
<body>
<svg class="journey" viewBox="0 0 1920 1080" xmlns="http://www.w3.org/2000/svg">
  <!-- road -->
  <g class="route">
    <path class="road" d="M55 551 H225 Q275 551 275 501 Q275 448 325 448 H445 Q495 448 495 498 V605 Q495 655 545 655 H665 Q715 655 715 605 V395 Q715 345 765 345 H888 Q938 345 938 395 V708 Q938 758 988 758 H1108 Q1158 758 1158 708 V498 Q1158 448 1208 448 H1330 Q1380 448 1380 498 V605 Q1380 655 1430 655 H1550 Q1600 655 1600 605 Q1600 551 1650 551 H1820"/>
    <path class="road-line" d="M55 551 H225 Q275 551 275 501 Q275 448 325 448 H445 Q495 448 495 498 V605 Q495 655 545 655 H665 Q715 655 715 605 V395 Q715 345 765 345 H888 Q938 345 938 395 V708 Q938 758 988 758 H1108 Q1158 758 1158 708 V498 Q1158 448 1208 448 H1330 Q1380 448 1380 498 V605 Q1380 655 1430 655 H1550 Q1600 655 1600 605 Q1600 551 1650 551 H1820"/>
  </g>

  <!-- scenes -->
  <g class="scenes">
    <rect class="scene" x="80" y="340" width="130" height="165" rx="16" fill="#e9c7c2" role="img" aria-label="Illustration of two parents taking a selfie"/>
    <rect class="scene" x="340" y="490" width="100" height="190" rx="16" fill="#f5b3a8" role="img" aria-label="Illustration of a happy student balancing books on his head"/>
    <rect class="scene" x="560" y="505" width="112" height="100" rx="16" fill="#efd3ea" role="img" aria-label="Illustration of two students walking with school bags"/>
    <rect class="scene" x="755" y="385" width="140" height="95" rx="16" fill="#dfe3f2" role="img" aria-label="Illustration of a student choosing a book from a shelf"/>
    <rect class="scene" x="995" y="545" width="112" height="175" rx="16" fill="#d9ece2" role="img" aria-label="Illustration of a student reading an open book"/>
    <rect class="scene" x="1190" y="495" width="155" height="130" rx="16" fill="#cfe6f3" role="img" aria-label="Illustration of a student beside a sailing ship on the sea"/>
    <rect class="scene" x="1435" y="510" width="145" height="110" rx="16" fill="#f6e7b8" role="img" aria-label="Illustration of a child reading among toy blocks"/>
    <rect class="scene" x="1645" y="505" width="235" height="215" rx="18" fill="#dcebef" role="img" aria-label="Illustration of students running back to a red school building"/>
  </g>

  <!-- labels -->
  <g class="labels">
    <text class="step-label" x="155" y="640">PARENT<tspan x="155" dy="29">INFORMATION</tspan></text>
    <text class="step-label" x="423" y="341">STUDENT<tspan x="423" dy="29">INFORMATION</tspan></text>
    <text class="step-label" x="646" y="722">APPROVING<tspan x="646" dy="29">EXCURSION</tspan></text>
    <text class="step-label" x="863" y="249">SCHOOL ACCEPTS<tspan x="863" dy="29">ALL THE UPDATE</tspan></text>
    <text class="step-label" x="1083" y="829">SCHOOL MANAGES<tspan x="1083" dy="29">THE EXCURSION</tspan></text>
    <text class="step-label" x="1300" y="347">SCHOOL TAKES THE<tspan x="1300" dy="29">CHILDREN TO THE EXCURSION</tspan></text>
    <text class="step-label" x="1540" y="722">SCHOOL<tspan x="1540" dy="29">CONDUCTS</tspan><tspan x="1540" dy="29">ACTIVITY</tspan></text>
    <text class="step-label" x="1750" y="438">STUDENTS<tspan x="1750" dy="29">RETURN</tspan><tspan x="1750" dy="29">TO SCHOOL</tspan></text>
  </g>

  <!-- pins -->
  <g class="pins">
    <a href="#parent-information"><g class="pin pin--pink">
      <path d="M112 712 L128 603 L144 712 Z"/>
      <circle class="pin-ring" cx="128" cy="768" r="60"/>
      <text class="pin-number" x="128" y="768">1</text>
    </g></a>
    <a href="#student-information"><g class="pin pin--olive">
      <path d="M369 302 L385 416 L401 302 Z"/>
      <circle class="pin-ring" cx="385" cy="247" r="60"/>
      <text class="pin-number" x="385" y="247">2</text>
    </g></a>
    <a href="#approving-excursion"><g class="pin pin--violet">
      <path d="M591 774 L607 660 L623 774 Z"/>
      <circle class="pin-ring" cx="607" cy="830" r="60"/>
      <text class="pin-number" x="607" y="830">3</text>
    </g></a>
    <a href="#school-updates"><g class="pin pin--sky">
      <path d="M811 198 L827 314 L843 198 Z"/>
      <circle class="pin-ring" cx="827" cy="143" r="60"/>
      <text class="pin-number" x="827" y="143">4</text>
    </g></a>
    <a href="#manage-excursion"><g class="pin pin--teal">
      <path d="M1032 902 L1048 790 L1064 902 Z"/>
      <circle class="pin-ring" cx="1048" cy="958" r="60"/>
      <text class="pin-number" x="1048" y="958">5</text>
    </g></a>
    <a href="#excursion-travel"><g class="pin pin--pink">
      <path d="M1252 302 L1268 414 L1284 302 Z"/>
      <circle class="pin-ring" cx="1268" cy="247" r="60"/>
      <text class="pin-number" x="1268" y="247">6</text>
    </g></a>
    <a href="#conduct-activity"><g class="pin pin--amber">
      <path d="M1474 799 L1490 688 L1506 799 Z"/>
      <circle class="pin-ring" cx="1490" cy="855" r="60"/>
      <text class="pin-number" x="1490" y="855">7</text>
    </g></a>
    <a href="#return-to-school"><g class="pin pin--violet">
      <path d="M1714 380 L1730 492 L1746 380 Z"/>
      <circle class="pin-ring" cx="1730" cy="325" r="60"/>
      <text class="pin-number" x="1730" y="325">8</text>
    </g></a>
  </g>
</svg>
</body>
</html>
```